Plotvista Caribbean

We need a vibrant, user friendly and exciting website for our land search company called "plotVista" This application will help individuals locate and or list lots for sale within the Caribbean. We will offer a small cash back incentive to buyers that purchase land from our site, and we will charge a 1%-2% success fee to our sellers once a successful transaction is made. We would like to become a match making site, matching buyers and sellers on our platform. We will also include a service directory and marketing advertisement spot for other service providers for a fee. We would like to see a webdesign incorporating Caribbean colors (blue, green and yellow) with very modern clean lines, very picturesque and easy to use.

Industry/Entity Type

Real Estate

Coding

Coded - Design and coding required

Number of Pages Required

5+ page

Font styles to use
Sans Serif

Colors
ffffff
85acd3
b768aa
dbdbdb

Requirements
Nice to have
• Scenic photos of the ocean and beautiful landscape

```html
<!DOCTYPE html>
<html lang="en">
<head>
<meta charset="utf-8">
<title>plotVista – Caribbean Land Search</title>
<link rel="stylesheet" href="https://fonts.googleapis.com/css2?family=Bellefair&family=Libre+Baskerville:wght@400;700&display=swap">
<style>
:root{
  --white:#ffffff;
  --blue:#85acd3;
  --purple:#b768aa;
  --grey:#dbdbdb;
  --ink:#1c1c1c;
  --muted:#8a8a8a;
  --body:#555555;
  --section:#f8f8f8;
}
*{margin:0;padding:0;box-sizing:border-box}
html,body{width:1200px;height:3571px;overflow:hidden}
body{background:var(--white);color:var(--ink);font-family:"Libre Baskerville",Georgia,serif;position:relative}
.heading{font-family:"Bellefair",Georgia,serif;font-weight:400}
.rule{width:150px;height:3px;background:var(--grey);margin:0 auto}

/* header + hero */
.hero{position:absolute;left:0;top:0;width:1200px;height:624px;
  background:linear-gradient(180deg,#f6ecc4 0%,#e9d6a4 18%,#b8b5a6 32%,#6d7b8e 44%,#3c4d5c 56%,#2f3c2c 68%,#4d5a2c 78%,#b39a45 88%,#d9b560 100%)}
.brand{position:absolute;left:219px;top:0;width:152px;height:90px;background:var(--purple);border-top:4px solid var(--blue);
  display:flex;align-items:center;justify-content:center;color:var(--white);font-family:"Bellefair",Georgia,serif;font-size:28px}
.main-nav{position:absolute;right:97px;top:36px;display:flex;gap:22px;font-family:"Libre Baskerville",serif;font-size:14px;color:#2a2a2a}
.main-nav a{color:inherit;text-decoration:none;padding-bottom:6px}
.main-nav a.active{border-bottom:2px solid var(--blue)}
.hero-title{position:absolute;left:0;width:1200px;top:258px;text-align:center;color:var(--white);font-size:66px}
.hero-sub{position:absolute;left:0;width:1200px;top:334px;text-align:center;color:var(--white);font-size:15px}
.search{position:absolute;left:331px;top:388px;width:536px;height:52px;border:2px solid var(--white);display:flex;align-items:center;justify-content:space-between;padding:0 6px 0 12px}
.search span{color:var(--white);font-size:13px}
.search button{background:var(--purple);color:var(--white);border:0;font:13px "Libre Baskerville",serif;width:110px;height:38px}
.dots{position:absolute;top:513px;left:0;width:1200px;display:flex;justify-content:center;gap:12px}
.dots i{width:12px;height:12px;border-radius:50%;background:var(--white)}
.dots i.on{background:var(--blue)}

/* welcome */
.welcome-band{position:absolute;left:0;top:624px;width:1200px;height:276px;
  background:linear-gradient(180deg,#c27fb6 0%,#b768aa 45%,#a85c9c 70%,#b97bb0 100%)}
.welcome-band h2{position:absolute;top:122px;width:100%;text-align:center;color:var(--white);font-size:32px}
.welcome-band .rule{position:absolute;top:198px;left:525px;background:var(--white)}
.notch{position:absolute;left:588px;top:898px}
.intro{position:absolute;top:950px;left:238px;width:724px;text-align:center;font-size:14px;line-height:29px;color:#444}
.btn{display:inline-flex;align-items:center;justify-content:center;color:var(--white);font:14px "Libre Baskerville",serif;text-decoration:none}
.btn-blue{background:var(--blue)}
.btn-purple{background:var(--purple)}
.intro-btn{position:absolute;left:521px;top:1130px;width:158px;height:53px}

/* what we do */
.services{position:absolute;top:1267px;left:0;width:1200px;height:787px;background:var(--section)}
.section-title{text-align:center;font-size:40px;color:var(--ink)}
.services .section-title{position:absolute;top:84px;width:100%}
.services .rule{position:absolute;top:163px;left:525px}
.cards{position:absolute;left:105px;display:flex;gap:23px}
.services .cards{top:240px}
.card{width:312px}
.photo{width:312px;height:226px}
.card h3{font-family:"Libre Baskerville",serif;font-weight:400;font-size:20px;margin-top:32px}
.card p{font-size:11px;line-height:19px;color:#aaa;margin-top:14px}
.card .btn{width:130px;height:41px;margin-top:44px;font-size:13px}

/* properties */
.properties .section-title{position:absolute;top:2125px;width:100%}
.properties .rule{position:absolute;top:2219px;left:525px}
.properties .cards{top:2268px}
.prop .photo{height:209px;border-bottom:5px solid var(--purple)}
.prop h3{font-family:"Bellefair",serif;font-size:26px;color:var(--purple);margin-top:22px}
.prop p{font-size:10px;line-height:16px;color:#777;margin-top:4px}
.seller{display:flex;align-items:center;gap:10px;margin-top:22px}
.avatar{width:48px;height:48px;border-radius:50%;background:linear-gradient(135deg,#c9b8a8,#7d6a5e)}
.seller small{display:block;color:var(--blue);font-family:"Bellefair",serif;font-size:17px}
.seller b{font-size:11px;color:#222}
.prop .btn{width:126px;height:40px;margin-top:14px;font-size:13px}

/* testimonials */
.testimonials{position:absolute;top:2810px;left:0;width:1200px;height:560px;border-top:4px solid var(--blue);
  background:linear-gradient(180deg,#f2f2f2 0%,#e6e6e6 50%,#ececec 100%)}
.testimonials .section-title{position:absolute;top:92px;width:100%}
.testimonials .rule{position:absolute;top:180px;left:525px;background:#c8c8c8}
.client{position:absolute;top:250px;width:100%;text-align:center;font-family:"Bellefair",serif;color:var(--purple);font-size:30px}
.client-meta{position:absolute;top:302px;width:100%;text-align:center;font-size:10px;font-weight:700}
.client-meta span{padding:0 6px}
.client-meta span+span{border-left:1px solid #333}
.quote{position:absolute;top:346px;left:238px;width:724px;text-align:center;font-size:14px;line-height:29px;color:#444}
.arrows{position:absolute;top:454px;left:0;width:100%;display:flex;justify-content:center;gap:18px}

/* footer */
.footer-line{position:absolute;top:3370px;left:0;width:1200px;height:4px;background:var(--purple)}
.footer-brand{position:absolute;top:3372px;left:524px;width:152px;height:91px;background:var(--purple);display:flex;align-items:center;justify-content:center;color:var(--white);font-family:"Bellefair",serif;font-size:28px}
.footer-nav{position:absolute;top:3502px;width:100%;display:flex;justify-content:center;gap:22px;font-size:13px}
.footer-nav a{color:#222;text-decoration:none}
.copyright{position:absolute;top:3542px;width:100%;text-align:center;font-size:12px}
.copyright span+span{border-left:1px solid #333;padding-left:6px;margin-left:6px}
</style>
</head>
<body>

<header class="hero" role="img" aria-label="Misty hills and forest above a golden meadow at sunrise">
  <div class="brand">plotVista</div>
  <nav class="main-nav">
    <a class="active" href="#">Home</a><a href="#">About Us</a><a href="#">Services</a><a href="#">Client's</a><a href="#">FAQ's</a><a href="#">Contact Us</a>
  </nav>
  <h1 class="hero-title heading">plotVista</h1>
  <p class="hero-sub">We help individuals locate and or list lots for sale within the Caribbean.</p>
  <form class="search"><span>Search Your Land</span><button type="button">Search Now</button></form>
  <div class="dots"><i class="on"></i><i></i><i></i><i></i></div>
</header>

<section class="welcome-band" role="img" aria-label="Field with trees under a purple tint">
  <h2 class="heading">Welcome To plotVista</h2>
  <div class="rule"></div>
</section>
<svg class="notch" width="24" height="14" viewBox="0 0 24 14"><path d="M0 0h24L12 14z" fill="#b570a9"/></svg>

<p class="intro">Sed ut perspiciatis unde omnis iste natus error sit voluptatem accusantium doloremque laudantium, totam rem aperiam, eaque ipsa quae ab illo inventore veritatis et quasi architecto beatae vitae dicta sunt explicabo. Nemo enim ipsam voluptatem quia voluptas sit aspernatur aut odit aut fugit, sed quia consequuntur magni dolores eos qui ratione voluptatem sequi nesciunt. Neque porro quisquam est, qui dolorem ipsum quia dolor sit amet, consectetur</p>
<a class="btn btn-blue intro-btn" href="#">Read More</a>

<section class="services">
  <h2 class="section-title heading">What We Do ?</h2>
  <div class="rule"></div>
  <div class="cards">
    <article class="card">
      <div class="photo" role="img" aria-label="Open commercial land at dusk" style="background:linear-gradient(180deg,#7fa4cf 0%,#b9c6d6 50%,#b59a80 75%,#8a6a50 100%)"></div>
      <h3>Commercial Land</h3>
      <p>Sed ut perspiciatis unde omnis iste natus error sit voluptatem accusantium doloremque laudantium, totam rem aperiam, eaque ipsa quae ab illo inventore</p>
      <a class="btn btn-blue" href="#">Read More</a>
    </article>
    <article class="card">
      <div class="photo" role="img" aria-label="Aerial view of a residential road junction" style="background:radial-gradient(circle at 50% 55%,#8a8f7a 0%,#4c6a3a 40%,#2f4a2a 100%)"></div>
      <h3>Residential Land</h3>
      <p>Sed ut perspiciatis unde omnis iste natus error sit voluptatem accusantium doloremque laudantium, totam rem aperiam, eaque ipsa quae ab illo inventore</p>
      <a class="btn btn-blue" href="#">Read More</a>
    </article>
    <article class="card">
      <div class="photo" role="img" aria-label="Business handshake over green farmland" style="background:linear-gradient(90deg,#6f8f4a 0%,#93a96a 45%,#7a5a3a 75%,#3e2e22 100%)"></div>
      <h3>Business Land</h3>
      <p>Sed ut perspiciatis unde omnis iste natus error sit voluptatem accusantium doloremque laudantium, totam rem aperiam, eaque ipsa quae ab illo inventore</p>
      <a class="btn btn-blue" href="#">Read More</a>
    </article>
  </div>
</section>

<section class="properties">
  <h2 class="section-title heading">Our Land Properties</h2>
  <div class="rule"></div>
  <div class="cards">
    <article class="card prop">
      <div class="photo" role="img" aria-label="Dry field with a for sale sign" style="background:linear-gradient(180deg,#9cb8dd 0%,#c7d6e6 35%,#9a8a5a 55%,#b99a62 100%)"></div>
      <h3>plotVista</h3>
      <p>Sed ut perspiciatis unde omnis iste natus error sit voluptatem accusantium doloremque laudantium</p>
      <div class="seller"><div class="avatar" role="img" aria-label="Seller portrait"></div><div><small>Seller</small><b>Marcus Reid</b></div></div>
      <a class="btn btn-purple" href="#">Buy Now</a>
    </article>
    <article class="card prop">
      <div class="photo" role="img" aria-label="Green field under a bright blue sky" style="background:linear-gradient(180deg,#1d5cb8 0%,#4d8fd8 35%,#a9c9e6 55%,#6f9a3a 70%,#4e7a2a 100%)"></div>
      <h3>plotVista</h3>
      <p>Sed ut perspiciatis unde omnis iste natus error sit voluptatem accusantium doloremque laudantium</p>
      <div class="seller"><div class="avatar" role="img" aria-label="Seller portrait"></div><div><small>Seller</small><b>Marcus Reid</b></div></div>
      <a class="btn btn-purple" href="#">Buy Now</a>
    </article>
    <article class="card prop">
      <div class="photo" role="img" aria-label="Golden farmland under a blue sky" style="background:linear-gradient(180deg,#3a52a8 0%,#7d93cf 40%,#c9cfe0 58%,#a8905a 72%,#8a7040 100%)"></div>
      <h3>plotVista</h3>
      <p>Sed ut perspiciatis unde omnis iste natus error sit voluptatem accusantium doloremque laudantium</p>
      <div class="seller"><div class="avatar" role="img" aria-label="Seller portrait"></div><div><small>Seller</small><b>Marcus Reid</b></div></div>
      <a class="btn btn-purple" href="#">Buy Now</a>
    </article>
  </div>
</section>

<section class="testimonials" role="img" aria-label="Faded beach with palm trees">
  <h2 class="section-title heading">What Customers Say About Us</h2>
  <div class="rule"></div>
  <p class="client">Daniel Moreau</p>
  <p class="client-meta"><span>plotVista</span><span>Member Since 2014</span></p>
  <p class="quote">Sed ut perspiciatis unde omnis iste natus error sit voluptatem accusantium doloremque laudantium, totam rem aperiam, eaque ipsa quae ab illo inventore veritatis et quasi architecto beatae vitae dicta sunt explicabo. Nemo enim ipsam voluptatem quia voluptas sit</p>
  <div class="arrows">
    <svg width="14" height="16" viewBox="0 0 14 16"><path d="M10 2 4 8l6 6" fill="none" stroke="#333" stroke-width="2.5"/></svg>
    <svg width="14" height="16" viewBox="0 0 14 16"><path d="m4 2 6 6-6 6" fill="none" stroke="#b768aa" stroke-width="2.5"/></svg>
  </div>
</section>

<footer>
  <div class="footer-line"></div>
  <div class="footer-brand">plotVista</div>
  <nav class="footer-nav"><a href="#">Home</a><a href="#">About Us</a><a href="#">Services</a><a href="#">Client's</a><a href="#">FAQ's</a><a href="#">Contact Us</a></nav>
  <p class="copyright"><span>© 2017 Company Name</span><span>All Rights Reserved</span></p>
</footer>

</body>
</html>
```